Holiday Rental Company Flyer Design (DL not A5)

Note from Brandloom Administration: The category sizing selected is A5, however the project requires DL sized artwork. Please refer to the DL template link below while the 'Special Requirements' are updated accordingly.

Project Brief:
We need a double sided DL flyer designed for an up market Holiday Rental Company that portrays a personalised approach to property management. These are to be used for letter box drops to homes we're specifically targeting so the design should be modern, complimentary colour palette, uncluttered & visually appealing.

Please Download the DL Template from Quillora here: http://www.quillora.com.au/ql/ns/propath/UploadResources.aspx?selectedTab=0?pfid=KMT&pf_id=KMT&xnav=easypath-upload-image#Templates

Target Market(s)

Wealthy Home Owners

Industry/Entity Type

It Company

Other font styles liked:
• Avant Garde Extra Light & Demi

Colors
33b8a4

Requirements
Must have
• DL Flyer sizes (210mm width x 99mm width, plus 3mm bleed)
• Front: Logo, Main Image & Grab
• Back: Contact Details & Brief Description of our business
• Images: Ideally the main image should be the house with the pool but alternatively a lifestyle images could also be used.
Nice to have
• A creative designer!
Should not have
• Clutter & busy designs

```html
<!DOCTYPE html>
<html lang="en">
<head>
<meta charset="utf-8">
<title>Harbourline Stays – DL Flyer</title>
<link rel="stylesheet" href="https://fonts.googleapis.com/css2?family=Questrial&family=Didact+Gothic&display=swap">
<style>
  :root {
    --teal: #33b8a4;
    --teal-dark: #1f7f71;
    --slate: #616366;
    --paper: #ffffff;
    --ink: #4a4a4a;
    --backdrop: #3a3a3c;
  }
  * { box-sizing: border-box; margin: 0; padding: 0; }
  html, body { width: 1200px; height: 750px; overflow: hidden; }
  body {
    background: var(--backdrop);
    font-family: "Didact Gothic", "Questrial", sans-serif;
    position: relative;
  }
  .flyer {
    position: absolute;
    left: 250px;
    width: 700px;
    height: 330px;
    background: var(--paper);
    overflow: hidden;
  }
  .flyer--front { top: 30px; }
  .flyer--back { top: 390px; }

  /* Front */
  .hero-photo {
    position: absolute;
    left: 20px; top: 20px; right: 20px; height: 250px;
    background:
      radial-gradient(ellipse at 25% 85%, rgba(240,180,90,.85), rgba(240,180,90,0) 45%),
      linear-gradient(160deg, #3b2f8f 0%, #5a4bb0 35%, #3e64c9 60%, #1f3f8a 80%, #2a2430 100%);
  }
  .brand-block {
    position: absolute;
    right: 80px; top: 60px;
    width: 130px; height: 130px;
    background: var(--teal);
    display: flex; align-items: center; justify-content: center;
    text-align: center;
  }
  .brand-name {
    font-family: "Questrial", sans-serif;
    color: var(--paper);
    font-size: 17px;
    letter-spacing: 3px;
    line-height: 1.3;
    text-transform: uppercase;
  }
  .tagline {
    position: absolute;
    left: 20px; right: 20px; bottom: 22px;
    text-align: right;
    font-family: "Questrial", sans-serif;
    font-size: 14px;
    letter-spacing: 5.5px;
    color: var(--ink);
    text-transform: uppercase;
  }
  .tagline__accent { color: var(--teal); }

  /* Back */
  .about-panel {
    position: absolute;
    left: 20px; top: 20px; width: 420px; height: 212px;
    background: var(--slate);
    color: var(--paper);
    padding: 22px 22px 0 22px;
    font-size: 10.5px;
    line-height: 1.45;
  }
  .about-panel h2 {
    font-family: "Questrial", sans-serif;
    font-size: 15px;
    font-weight: 700;
    margin-bottom: 8px;
  }
  .about-panel p { margin-bottom: 7px; }
  .about-panel ul { padding-left: 14px; }
  .interior-photo {
    position: absolute;
    left: 440px; top: 20px; right: 20px; height: 212px;
    background: linear-gradient(135deg, #b9bcbb 0%, #d8d9d7 45%, #eeeeec 70%, #a9acab 100%);
  }
  .contact-band {
    position: absolute;
    left: 20px; top: 232px; right: 20px; height: 46px;
    background: var(--teal);
    color: var(--paper);
    display: flex; align-items: center; justify-content: space-between;
    padding: 0 18px 0 22px;
  }
  .contact-band__lead { font-size: 10.5px; line-height: 1.35; max-width: 360px; }
  .contact-band__lead strong { font-weight: 700; }
  .contact-band__phone {
    font-family: "Questrial", sans-serif;
    font-size: 24px;
    letter-spacing: 1px;
    display: flex; align-items: center; gap: 8px;
  }
  .ribbon-fold { position: absolute; left: 20px; top: 278px; }
  .details-row {
    position: absolute;
    left: 42px; right: 20px; bottom: 16px;
    display: flex; gap: 26px;
    font-size: 11px; color: var(--ink);
  }
  .details-row__item { display: flex; align-items: center; gap: 6px; }
  .details-row__item--address { margin-left: auto; }
</style>
</head>
<body>

<section class="flyer flyer--front">
  <div class="hero-photo" role="img" aria-label="Evening photograph of a modern holiday home with a lit pool and warm interior lights"></div>
  <div class="brand-block">
    <span class="brand-name">Harbourline<br>Stays</span>
  </div>
  <p class="tagline">Holiday Rental Management <span class="tagline__accent">With a Difference</span></p>
</section>

<section class="flyer flyer--back">
  <div class="about-panel">
    <h2>What We Do Differently!</h2>
    <p>Rather than relying upon a key safe or a central pick-up destination, a ‘Harbourline Stays’ staff member will greet guests upon arrival.</p>
    <p>Our ‘<strong>Meet &amp; Greet</strong>’ service provides home owners with an increased level of security and also allows us to:</p>
    <ul>
      <li>Prepare the home for their arrival (lights, heaters, music etc.)</li>
      <li>Establish a rapport &amp; help facilitate future bookings</li>
      <li>Reiterate their responsibilities to ensure the return of their bond</li>
    </ul>
  </div>
  <div class="interior-photo" role="img" aria-label="Photograph of a bright tiled bathroom with a freestanding bath and white flowers"></div>

  <div class="contact-band">
    <p class="contact-band__lead">If you’d like to know what your property could achieve or require additional information, <strong>please contact us on:</strong></p>
    <p class="contact-band__phone">
      <svg width="18" height="18" viewBox="0 0 24 24" aria-hidden="true"><path fill="#fff" d="M6.6 10.8a15.1 15.1 0 0 0 6.6 6.6l2.2-2.2c.3-.3.7-.4 1-.2 1.1.4 2.3.6 3.6.6.6 0 1 .4 1 1V20c0 .6-.4 1-1 1A17 17 0 0 1 3 4c0-.6.4-1 1-1h3.5c.6 0 1 .4 1 1 0 1.3.2 2.5.6 3.6.1.3 0 .7-.2 1z"/></svg>
      (03) 5550 1274
    </p>
  </div>
  <svg class="ribbon-fold" width="14" height="12" viewBox="0 0 14 12" aria-hidden="true"><polygon points="0,0 14,0 14,12" fill="var(--teal-dark)"/></svg>

  <div class="details-row">
    <span class="details-row__item">
      <svg width="13" height="10" viewBox="0 0 13 10" aria-hidden="true"><rect x="0.5" y="0.5" width="12" height="9" fill="none" stroke="#555"/><polyline points="0.5,0.5 6.5,5.5 12.5,0.5" fill="none" stroke="#555"/></svg>
      stay@harbourlinestays.com.au
    </span>
    <span class="details-row__item">
      <svg width="12" height="12" viewBox="0 0 12 12" aria-hidden="true"><circle cx="6" cy="6" r="5.5" fill="none" stroke="#555"/><ellipse cx="6" cy="6" rx="2.5" ry="5.5" fill="none" stroke="#555"/><line x1="0.5" y1="6" x2="11.5" y2="6" stroke="#555"/></svg>
      harbourlinestays.com.au
    </span>
    <span class="details-row__item details-row__item--address">
      <svg width="10" height="13" viewBox="0 0 10 13" aria-hidden="true"><path d="M5 0a5 5 0 0 1 5 5c0 3.5-5 8-5 8S0 8.5 0 5a5 5 0 0 1 5-5z" fill="#555"/><circle cx="5" cy="5" r="1.8" fill="#fff"/></svg>
      PO Box 12, Elmsbay Victoria 3999
    </span>
  </div>
</section>

</body>
</html>
```